Cozy Cradle Loops Needs a Beautiful Website

I need a new website for this new E-commerce. I sell handmade baby crochets, e.g. booties, headbands, hats, etc. I need a feminine and soft design to make the moms-to-be say 'oohh ahh'. I'd like pink, blue and gray. I'd like an inviting homepage, and nice regular pages where people can see and order the products.

Industry/Entity Type

Baby

Requirements
Must have
• beautiful, soft, feminine design. Please use pictures of the colors I'd like: brown, yellow, pink and blue. Any combination, but definitely include brown.

```html
<!DOCTYPE html>
<html lang="en">
<head>
<meta charset="utf-8">
<title>Cozy Cradle Loops</title>
<link href="https://fonts.googleapis.com/css2?family=Lobster&family=Open+Sans:wght@400;600&family=Roboto:wght@300;400&display=swap" rel="stylesheet">
<style>
:root{
  --pink:#e8378a;
  --pink-dark:#c92672;
  --blue:#33bde3;
  --blue-dark:#1f9fd0;
  --orange:#f7941d;
  --dark:#2d2d2d;
  --darker:#242424;
  --grey:#8a8a8a;
  --text:#555;
  --white:#fff;
  --line:#e6e6e6;
}
*{margin:0;padding:0;box-sizing:border-box}
html,body{width:673px;height:1200px;overflow:hidden;background:#fff}
body{font-family:'Open Sans',sans-serif;color:var(--text);position:relative}
.abs{position:absolute}
.script{font-family:'Lobster',cursive}

.site-header{left:0;top:0;width:673px;height:158px}
.header-scene{left:31px;top:0;width:605px;height:158px;border-radius:0 0 0 0;
  background:linear-gradient(180deg,#fff 0%,#fff 45%,#e6f2c6 62%,#a7d13a 78%,#7fb71f 100%)}
.top-links{right:42px;top:18px;display:flex;gap:23px;font-size:9.5px;color:#777}
.brand{left:33px;top:28px;font-family:'Lobster',cursive;font-size:27px;color:var(--pink);line-height:1}

.main-nav{left:31px;top:158px;width:533px;height:32px;background:var(--pink);border:2px solid #f25aa0;display:flex;align-items:center;padding-left:12px}
.main-nav a{font-family:'Lobster',cursive;color:#fff;font-size:13px;text-decoration:none;padding:0 16px 0 0;margin-right:16px;border-right:1px solid rgba(255,255,255,.35);line-height:20px}
.main-nav a:last-child{border:none}
.nav-btn{top:158px;width:31px;height:32px;display:flex;align-items:center;justify-content:center}
.btn-search{left:567px;background:var(--blue);border:2px solid #7ad6ef}
.btn-cart{left:602px;background:var(--orange);border:2px solid #fbb660;width:34px}

.hero{left:31px;top:210px;width:605px;height:280px;background:linear-gradient(100deg,#8fb2c4 0%,#e9c95c 30%,#f3dc8a 45%,#d8a27f 60%,#5bc3e4 85%,#e6a6b6 100%)}
.hero-arrow{width:24px;height:24px;border-radius:50%;background:rgba(40,40,40,.75);display:flex;align-items:center;justify-content:center;top:346px}
.hero-card{left:345px;top:230px;width:246px;height:246px;border-radius:50%;background:rgba(255,255,255,.85);text-align:center;padding-top:40px}
.hero-brand{font-family:'Lobster',cursive;color:var(--pink);font-size:22px}
.hero-title{font-family:'Lobster',cursive;color:#3a3a3a;font-size:27px;margin-top:8px}
.hero-text{font-size:7.5px;line-height:13px;color:#888;margin:10px auto 0;width:180px}
.hero-basket{width:30px;height:30px;border-radius:50%;background:var(--pink);margin:12px auto 0;display:flex;align-items:center;justify-content:center}

.category{top:510px;width:193px;height:112px;border:1px solid var(--line);padding:2px}
.category .photo{width:100%;height:100%;position:relative;display:flex;flex-direction:column;align-items:center;justify-content:center}
.category .ico{width:30px;height:30px;border-radius:50%;background:rgba(60,60,60,.7);border:2px solid rgba(255,255,255,.6);display:flex;align-items:center;justify-content:center}
.category .name{font-family:'Lobster',cursive;color:#fff;font-size:17px;margin-top:2px}

.section-title{left:30px;top:636px;font-family:'Lobster',cursive;color:var(--pink);font-size:18px}
.pager{top:645px;width:13px;height:13px;border-radius:50%;border:1px solid #ccc;font-size:8px;line-height:11px;text-align:center;color:#777}

.product{top:675px;width:143px;height:206px;border:1px solid var(--line);background:#fff}
.product .photo{height:103px}
.product .info{padding:10px 11px 0}
.product .row{display:flex;justify-content:space-between;align-items:center}
.product h3{font-family:'Roboto',sans-serif;font-weight:300;font-size:13px;color:#555}
.stars{color:#f5a623;font-size:7px;letter-spacing:-.5px}
.stars span{color:#ccc}
.product p{font-size:8px;line-height:13px;color:#999;margin-top:10px}
.price{position:absolute;left:0;right:0;bottom:0;height:26px;background:var(--pink);color:#fff;display:flex;justify-content:space-between;align-items:center;padding:0 11px;font-family:'Roboto',sans-serif;font-size:11px}

.footer-info{left:31px;top:905px;width:605px;height:164px;background:var(--blue)}
.footer-brand{left:44px;top:925px;font-family:'Lobster',cursive;font-size:19px;color:#fff}
.contact-row{left:43px;display:flex;align-items:center;gap:14px;color:#fff;font-size:8.5px;line-height:14px}
.contact-ico{width:21px;height:21px;border:1px solid rgba(255,255,255,.7);display:flex;align-items:center;justify-content:center}
.footer-col{top:930px;color:#fff}
.footer-col h4{font-family:'Roboto',sans-serif;font-weight:400;font-size:11.5px;margin-bottom:12px}
.footer-col li{list-style:none;font-size:7.5px;line-height:14.5px}

.footer-bar{left:31px;top:1069px;width:605px;height:99px;background:var(--dark)}
.footer-bottom{left:31px;top:1127px;width:605px;height:41px;background:var(--darker);border-top:1px solid #3a3a3a}
.news-ico{left:41px;top:1080px;width:30px;height:30px;border-radius:50%;border:1px solid #444;display:flex;align-items:center;justify-content:center}
.news-label{left:82px;top:1083px;color:#ddd;font-size:8.5px;line-height:13px;letter-spacing:.3px}
.news-input{left:155px;top:1086px;width:117px;height:22px;background:#333;border:1px solid #3d3d3d;color:#777;font-size:6.5px;padding:7px 9px}
.news-btn{left:280px;top:1085px;width:56px;height:24px;background:var(--blue-dark);color:#fff;font-size:7.5px;font-weight:600;display:flex;align-items:center;justify-content:center;border-radius:2px}
.pay-label{left:367px;top:1092px;color:#ddd;font-size:8.5px;letter-spacing:.3px}
.pay-card{top:1087px;width:32px;height:20px;background:#cfcfcf;border:1px solid #888;border-radius:2px}
.copy{left:44px;top:1142px;color:#999;font-size:7.5px}
.social{top:1136px;width:18px;height:18px;border-radius:50%;border:1px solid #666}
.legal{right:43px;top:1142px;color:#999;font-size:7.5px}
</style>
</head>
<body>

<header class="site-header abs">
  <div class="header-scene abs" role="img" aria-label="Illustrated meadow with rainbow, trees and stars"></div>
  <nav class="top-links abs"><span>My Account</span><span>Create an Account</span><span>Log in</span></nav>
  <div class="brand abs">Cozy Cradle Loops</div>
</header>

<nav class="main-nav abs">
  <a>Home</a><a>Baby Crochets</a><a>Booties &amp; Accessories</a><a>Headbands</a><a>Selling</a><a>Contact</a>
</nav>
<div class="nav-btn btn-search abs"><svg width="11" height="11" viewBox="0 0 12 12"><circle cx="5" cy="5" r="3.8" fill="none" stroke="#fff" stroke-width="1.4"/><line x1="8" y1="8" x2="11" y2="11" stroke="#fff" stroke-width="1.4"/></svg></div>
<div class="nav-btn btn-cart abs"><svg width="15" height="13" viewBox="0 0 16 14"><path d="M1 1h2.5l2 8h8l1.5-6H4.3" fill="none" stroke="#fff" stroke-width="1.5"/><circle cx="6.5" cy="12" r="1.3" fill="#fff"/><circle cx="12.5" cy="12" r="1.3" fill="#fff"/></svg></div>

<section class="hero abs" role="img" aria-label="Photo of a baby in a yellow knitted hood"></section>
<div class="hero-arrow abs" style="left:62px"><svg width="8" height="10" viewBox="0 0 8 10"><path d="M6 1L2 5l4 4" fill="none" stroke="#fff" stroke-width="1.6"/></svg></div>
<div class="hero-arrow abs" style="left:590px"><svg width="8" height="10" viewBox="0 0 8 10"><path d="M2 1l4 4-4 4" fill="none" stroke="#fff" stroke-width="1.6"/></svg></div>
<div class="hero-card abs">
  <div class="hero-brand">Cozy Cradle Loops</div>
  <div class="hero-title">Baby crochets</div>
  <p class="hero-text">Lorem ipsum dolor sit amet, consectetur adipisicing elit, sed do eiusmod tempor incididunt ut labore et dolore magna aliqua.</p>
  <div class="hero-basket"><svg width="13" height="11" viewBox="0 0 14 12"><path d="M1 4h12l-1.5 7h-9z" fill="#fff"/><path d="M4 4l3-3 3 3" fill="none" stroke="#fff" stroke-width="1.2"/></svg></div>
</div>

<div class="category abs" style="left:31px"><div class="photo" role="img" aria-label="Photo of blue crochet baby sneakers" style="background:linear-gradient(135deg,#8c8c8c,#3b4463 55%,#6d6d6d)"><div class="ico"><svg width="12" height="10" viewBox="0 0 16 14"><path d="M1 1h2.5l2 8h8l1.5-6H4.3" fill="none" stroke="#fff" stroke-width="1.6"/></svg></div><div class="name">Sneaker Blue</div></div></div>
<div class="category abs" style="left:237px"><div class="photo" role="img" aria-label="Photo of ivory crochet booties with roses" style="background:linear-gradient(135deg,#9a9a95,#e9e6da 50%,#c9b9a8)"><div class="ico"><svg width="12" height="10" viewBox="0 0 16 14"><path d="M1 1h2.5l2 8h8l1.5-6H4.3" fill="none" stroke="#fff" stroke-width="1.6"/></svg></div><div class="name">Ivory Shows</div></div></div>
<div class="category abs" style="left:442px"><div class="photo" role="img" aria-label="Photo of pink crochet ballet slippers" style="background:linear-gradient(135deg,#b5a9a9,#f0c3cf 50%,#d9a1b3)"><div class="ico"><svg width="12" height="10" viewBox="0 0 16 14"><path d="M1 1h2.5l2 8h8l1.5-6H4.3" fill="none" stroke="#fff" stroke-width="1.6"/></svg></div><div class="name">Pink Ballet</div></div></div>

<h2 class="section-title abs">Featured Products</h2>
<div class="pager abs" style="left:603px">‹</div>
<div class="pager abs" style="left:621px">›</div>

<article class="product abs" style="left:31px"><div class="photo" role="img" aria-label="Photo of a pink crochet crown headband" style="background:linear-gradient(160deg,#fafafa,#f59ad9 55%,#f2f2f2)"></div><div class="info"><div class="row"><h3>Baby Crochets</h3><span class="stars">★★★<span>★</span></span></div><p>Pellentesque habitant morbi triique senectus et netus</p></div><div class="price"><span>$7.99</span><svg width="10" height="9" viewBox="0 0 14 12"><path d="M1 4h12l-1.5 7h-9z" fill="#fff"/></svg></div></article>
<article class="product abs" style="left:184px"><div class="photo" role="img" aria-label="Photo of pink crochet ballet booties" style="background:linear-gradient(160deg,#e9e4dc,#f1bccb 55%,#ddd)"></div><div class="info"><div class="row"><h3>Pink ballet</h3><span class="stars">★★★<span>★</span></span></div><p>Pellentesque habitant morbi triique senectus et netus</p></div><div class="price"><span>$7.99</span><svg width="10" height="9" viewBox="0 0 14 12"><path d="M1 4h12l-1.5 7h-9z" fill="#fff"/></svg></div></article>
<article class="product abs" style="left:338px"><div class="photo" role="img" aria-label="Photo of black crochet baby sneakers" style="background:linear-gradient(160deg,#9a9a9a,#2b2b2b 55%,#888)"></div><div class="info"><div class="row"><h3>Sneaker black</h3><span class="stars">★★★<span>★</span></span></div><p>Pellentesque habitant morbi triique senectus et netus</p></div><div class="price"><span>$7.99</span><svg width="10" height="9" viewBox="0 0 14 12"><path d="M1 4h12l-1.5 7h-9z" fill="#fff"/></svg></div></article>
<article class="product abs" style="left:491px"><div class="photo" role="img" aria-label="Photo of brown crochet baby sneakers" style="background:linear-gradient(160deg,#d9a0a8,#5b4338 55%,#bbb)"></div><div class="info"><div class="row"><h3>Sneaker gray</h3><span class="stars">★★★<span>★</span></span></div><p>Pellentesque habitant morbi triique senectus et netus</p></div><div class="price"><span>$7.99</span><svg width="10" height="9" viewBox="0 0 14 12"><path d="M1 4h12l-1.5 7h-9z" fill="#fff"/></svg></div></article>

<footer>
  <div class="footer-info abs"></div>
  <div class="footer-brand abs">Cozy Cradle Loops</div>
  <div class="contact-row abs" style="top:969px"><div class="contact-ico"><svg width="9" height="12" viewBox="0 0 10 13"><path d="M5 12S1 7 1 4.5a4 4 0 018 0C9 7 5 12 5 12z" fill="none" stroke="#fff" stroke-width="1.2"/><circle cx="5" cy="4.5" r="1.3" fill="#fff"/></svg></div><span>14 Willow Lane Hollybrook<br>Cozy Cradle Loops HB2 4LM</span></div>
  <div class="contact-row abs" style="top:1003px"><div class="contact-ico"><svg width="11" height="11" viewBox="0 0 12 12"><path d="M2 3c0-1 1-2 2-2h4c1 0 2 1 2 2v1H8V3H4v1H2zM2 5h8v5H2z" fill="#fff"/></svg></div><span>Phone : 10 482 67 205 913</span></div>
  <div class="contact-row abs" style="top:1034px"><div class="contact-ico"><svg width="12" height="9" viewBox="0 0 12 9"><rect x=".6" y=".6" width="10.8" height="7.8" fill="none" stroke="#fff" stroke-width="1.1"/><path d="M1 1l5 4 5-4" fill="none" stroke="#fff" stroke-width="1.1"/></svg></div><span style="font-size:10px">hello@cozycradleloops.com</span></div>

  <div class="footer-col abs" style="left:248px"><h4>INFORMATION</h4><ul><li>Baby Shoes</li><li>Baby crochets</li><li>booties</li><li>headbands</li></ul></div>
  <div class="footer-col abs" style="left:385px"><h4>CUSTOMER SUPPORT</h4><ul><li>Contact Us</li><li>Shipping &amp; Returns</li><li>Privacy Notice</li><li>Conditions of Use</li></ul></div>
  <div class="footer-col abs" style="left:553px"><h4>MY ACCOUNT</h4><ul><li>My Rewards</li><li>Register</li><li>About Rewards</li><li>Rewards FAQ</li></ul></div>

  <div class="footer-bar abs"></div>
  <div class="news-ico abs"><svg width="15" height="11" viewBox="0 0 12 9"><rect x=".6" y=".6" width="10.8" height="7.8" fill="none" stroke="#aaa" stroke-width="1"/><path d="M1 1l5 4 5-4" fill="none" stroke="#aaa" stroke-width="1"/></svg></div>
  <div class="news-label abs">NEWSLETTER<br>SIGN UP</div>
  <div class="news-input abs">Enter Your Email</div>
  <div class="news-btn abs">SUBSCRIBE</div>
  <div class="pay-label abs">PAYMENTS</div>
  <div class="pay-card abs" style="left:430px"></div>
  <div class="pay-card abs" style="left:469px"></div>
  <div class="pay-card abs" style="left:508px"></div>
  <div class="pay-card abs" style="left:547px"></div>
  <div class="pay-card abs" style="left:586px"></div>
  <div class="footer-bottom abs"></div>
  <div class="copy abs">©2013 - 2014 Cozy Cradle Loops., All Rights Reserved.</div>
  <div class="social abs" style="left:332px"></div>
  <div class="social abs" style="left:356px"></div>
  <div class="social abs" style="left:380px"></div>
  <div class="legal abs">Terms of Service | Privacy Policy</div>
</footer>

</body>
</html>
```